Meridale Bed Company Needs Business Card

Looking for a very nice looking business card. Creative but not extravagant. We sell beds and pillows across the U.S. and need something professional but catchy. I have attached the logo.

Name : Devin Holt
Title : President
Phone : (800) 471-2960
Email: hello@quilmora.com
Website: www.quilmora.com

Can be single-sided or double-sided
horizontal or vertical

Can use Blues/Greys

Target Market(s)

Mass Market

Industry/Entity Type

Retail

Contact Information for Business Card

Name : Devin Holt
Title : President
Phone : (800) 471-2960
Email: hello@quilmora.com
Website: www.quilmora.com

Requirements
Must have
• Clean, Modern, Smooth
• Can use Blues/Greys
• On the other side without the information - have something simple like www.quilmora.com or our logo
Nice to have
• Surprise me
Should not have
• Nothing crazy, nothing cluttered

```html
<!DOCTYPE html>
<html lang="en">
<head>
<meta charset="utf-8">
<title>Quilmora Business Card</title>
<link rel="stylesheet" href="https://fonts.googleapis.com/css2?family=Open+Sans:ital,wght@0,300;0,400;0,700;1,400&display=swap">
<style>
  :root {
    --bg-top: #2f3f48;
    --bg-bottom: #283841;
    --card-dark: #434343;
    --card-white: #f4f4f4;
    --label-white: #e4e2df;
    --brand-blue: #3ea6d8;
    --fold-blue: #2a7fa9;
    --text-light: #f2f2f2;
  }
  * { margin: 0; padding: 0; box-sizing: border-box; }
  html, body { width: 1200px; height: 900px; overflow: hidden; }
  body {
    background: linear-gradient(180deg, var(--bg-top), var(--bg-bottom));
    font-family: "Open Sans", sans-serif;
    position: relative;
  }
  .card {
    position: absolute;
    left: 260px;
    width: 680px;
    height: 390px;
    border-radius: 3px;
    overflow: hidden;
    box-shadow: 0 12px 30px rgba(0,0,0,.35);
  }
  .card-back { top: 40px; background: var(--card-dark); }
  .card-front { top: 470px; background: var(--card-white); }
  .card-shapes { position: absolute; inset: 0; }

  .brand-label {
    position: absolute;
    left: 190px; top: 48px;
    width: 300px; height: 150px;
    display: flex; align-items: center; justify-content: center;
  }
  .wordmark {
    font-family: "Open Sans", sans-serif;
    font-weight: 300;
    color: var(--brand-blue);
    letter-spacing: 1px;
    line-height: 1;
  }
  .brand-label .wordmark { font-size: 52px; position: relative; }
  .front-wordmark {
    position: absolute;
    left: 350px; width: 330px; top: 150px;
    text-align: center;
    font-size: 48px;
  }

  .identity { position: absolute; left: 52px; top: 64px; color: var(--text-light); }
  .identity-name { font-size: 26px; font-weight: 700; line-height: 1.1; }
  .identity-title { font-size: 16px; font-style: italic; margin-top: 2px; }

  .contact-list { position: absolute; left: 34px; top: 186px; list-style: none; }
  .contact-item {
    display: flex; align-items: center; gap: 14px;
    color: var(--text-light);
    font-size: 22px;
    height: 38px;
  }
  .contact-item svg { width: 24px; height: 24px; flex: none; }
</style>
</head>
<body>

<section class="card card-back" aria-label="Card back">
  <svg class="card-shapes" viewBox="0 0 680 390" aria-hidden="true">
    <rect x="0" y="82" width="680" height="52" fill="var(--brand-blue)"/>
    <polygon points="190,48 178,48 190,62" fill="#9a9896"/>
    <polygon points="490,48 502,48 490,62" fill="#9a9896"/>
    <rect x="190" y="48" width="300" height="150" fill="var(--label-white)"/>
  </svg>
  <div class="brand-label"><span class="wordmark">quilmora</span></div>
</section>

<section class="card card-front" aria-label="Card front">
  <svg class="card-shapes" viewBox="0 0 680 390" aria-hidden="true">
    <polygon points="0,0 340,0 340,316 282,390 0,390" fill="var(--card-dark)"/>
    <polygon points="250,316 340,316 282,390 250,390" fill="var(--brand-blue)"/>
    <polygon points="332,128 350,128 336,150" fill="var(--fold-blue)"/>
    <rect x="0" y="58" width="350" height="70" fill="var(--brand-blue)"/>
  </svg>

  <div class="identity">
    <p class="identity-name">Devin Holt</p>
    <p class="identity-title">President</p>
  </div>

  <ul class="contact-list">
    <li class="contact-item">
      <svg viewBox="0 0 24 24" aria-hidden="true"><rect x="1" y="1" width="22" height="22" rx="3" fill="var(--brand-blue)"/><path d="M9 5c-2 1-3 3-2 7s3 7 6 8l2-3-2-2-2 1c-1-1-2-3-2-5l2-1-1-3z" fill="var(--card-dark)"/></svg>
      <span>(800) 471-2960</span>
    </li>
    <li class="contact-item">
      <svg viewBox="0 0 24 24" fill="none" stroke="var(--brand-blue)" stroke-width="1.4" aria-hidden="true"><circle cx="12" cy="12" r="10"/><ellipse cx="12" cy="12" rx="4.5" ry="10"/><path d="M2 12h20M4 7h16M4 17h16"/></svg>
      <span>www.quilmora.com</span>
    </li>
    <li class="contact-item">
      <svg viewBox="0 0 24 24" fill="none" stroke="var(--brand-blue)" stroke-width="1.4" aria-hidden="true"><rect x="2" y="5" width="20" height="14"/><path d="M2 5l10 8 10-8M2 19l7-7M22 19l-7-7"/></svg>
      <span>hello@quilmora.com</span>
    </li>
  </ul>

  <p class="wordmark front-wordmark">quilmora</p>
</section>

</body>
</html>
```